Moravel Aesthetic Doctor

I require an elegant, luxurious looking business card for my aesthetic business. I am a doctor and that will set me aside from competitors. I am planning to provide home and spa based treatments to clients with high expectations. I have attached my logo.

```html
<!DOCTYPE html>
<html lang="en">
<head>
<meta charset="utf-8">
<title>Moravel Aesthetic Doctor – Business Card</title>
<link href="https://fonts.googleapis.com/css2?family=Roboto:wght@300;400;500&display=swap" rel="stylesheet">
<style>
  :root {
    --backdrop: #5a5a5c;
    --card: #313133;
    --edge: #6cc4ee;
    --accent: #5ab8e8;
    --silver: #c9c9cc;
    --muted: #a9a9ad;
    --white: #f2f2f2;
    --rule: #8a8a8e;
  }
  * { box-sizing: border-box; margin: 0; padding: 0; }
  html, body {
    width: 1200px; height: 1124px; overflow: hidden;
    background: var(--backdrop);
    font-family: "Roboto", Arial, sans-serif;
  }
  .card {
    position: absolute; left: 170px;
    width: 860px; height: 492px;
    background: var(--card);
    border-bottom: 5px solid var(--edge);
    border-left: 3px solid var(--edge);
    box-shadow: 0 10px 28px rgba(0,0,0,.35);
  }
  .card--back { top: 48px; }
  .card--front { top: 584px; }

  .brand { display: flex; align-items: center; gap: 22px; }
  .brand__mark {
    width: 92px; height: 92px; border-radius: 50%;
    border: 3px solid var(--silver); flex: none;
  }
  .brand__name {
    color: var(--silver); font-weight: 300; line-height: 1;
  }
  .brand__title { font-size: 58px; letter-spacing: 4px; text-transform: uppercase; }
  .brand__sub { font-size: 23px; letter-spacing: 3px; text-transform: uppercase; margin-top: 6px; }

  .card--back .brand { position: absolute; left: 200px; top: 120px; }
  .services {
    position: absolute; left: 0; right: 0; top: 290px;
    text-align: center; color: var(--white);
    font-size: 22px; font-weight: 300; line-height: 1.45;
  }

  .card--front .brand { position: absolute; right: 70px; top: 50px; }
  .holder { position: absolute; left: 90px; top: 198px; }
  .holder__name { color: var(--accent); font-size: 30px; font-weight: 500; }
  .holder__name small { font-size: 18px; margin-left: 4px; }
  .holder__role { color: var(--muted); font-size: 21px; font-weight: 300; margin-top: 4px; }
  .divider {
    position: absolute; left: 90px; right: 90px; top: 290px;
    border-top: 1.5px solid var(--rule);
  }
  .contacts { position: absolute; left: 90px; top: 312px; list-style: none; }
  .contacts li {
    display: flex; align-items: center; gap: 16px;
    color: var(--muted); font-size: 21px; font-weight: 300; height: 32px;
  }
  .contacts svg { width: 20px; height: 20px; fill: none; stroke: var(--accent); stroke-width: 1.8; }
  .contacts .link { color: var(--accent); }
  .social { position: absolute; right: 70px; bottom: 40px; display: flex; gap: 20px; }
  .social span { width: 30px; height: 30px; border-radius: 50%; background: var(--accent); }
</style>
</head>
<body>

<section class="card card--back">
  <div class="brand">
    <span class="brand__mark"></span>
    <div class="brand__name">
      <div class="brand__title">Moravel</div>
      <div class="brand__sub">Aesthetic Doctor</div>
    </div>
  </div>
  <p class="services">
    Dermal injectables • Plasma facials • Microneedling<br>
    Skin boosters • Excessive sweating<br>
    Home and Spa Based Treatments
  </p>
</section>

<section class="card card--front">
  <div class="brand">
    <span class="brand__mark"></span>
    <div class="brand__name">
      <div class="brand__title">Moravel</div>
      <div class="brand__sub">Aesthetic Doctor</div>
    </div>
  </div>
  <div class="holder">
    <h1 class="holder__name">Dr Elena Varsk, <small>MRCPCH MD</small></h1>
    <p class="holder__role">Australasian Diploma of Aesthetic Medicine</p>
  </div>
  <div class="divider"></div>
  <ul class="contacts">
    <li>
      <svg viewBox="0 0 24 24"><path d="M5 3h4l2 5-2.5 1.5a11 11 0 0 0 6 6L16 13l5 2v4a2 2 0 0 1-2 2A17 17 0 0 1 3 5a2 2 0 0 1 2-2z"/></svg>
      0800 555 014
    </li>
    <li>
      <svg viewBox="0 0 24 24"><rect x="3" y="5" width="18" height="14" rx="1"/><path d="M3 6l9 7 9-7"/></svg>
      elena@moravel.co.nz
    </li>
    <li>
      <svg viewBox="0 0 24 24"><circle cx="12" cy="12" r="9"/><path d="M3 12h18M12 3c3 3 3 15 0 18M12 3c-3 3-3 15 0 18"/></svg>
      <span>www.<span class="link">moravel</span>.co.nz</span>
    </li>
  </ul>
  <div class="social"><span></span><span></span></div>
</section>

</body>
</html>
```